Varsity Purse Wordpress Website (re)design

we are a student run financial literacy website and are desperately trying to get college students to pay attention to the finances to create solid financial skills for life. This age group LOVES pixolette so instead of sharing a lot of text we want to tease through graphics/infographics topics that are relevant to them based on what their peers are discussing and then push them to our resources to learn more. ultimately we will also recommend products to them that are carefully selected by us. these will range from a book on paying back their student loan to a place to store their dorm stuff when they go home for summer break to a credit card we determine is best for them. So yes, commerce is imp but SEO to attract students comes first which we will do through survey monkey and cash prizes. we need to capture email address. we also have a "checklist" (attached and needs rebranding) of the basic and most imp money matters for them. Each item will hyperlink to our parnter, nuvoe, and need to do so seamlessly and push them back to us.

Target Market(s)

college students and young adults

Requirements
Must have
• simple, clean and graphic with an integration of survey monkey, an borvel store and a capture of emails through mailchimp or other similar. Ability to edit after ourselves on wordpress

```html
<!DOCTYPE html>
<html lang="en">
<head>
<meta charset="utf-8">
<title>Varsity Purse — Take Charge of Your Change</title>
<link rel="stylesheet" href="https://fonts.googleapis.com/css2?family=Open+Sans:wght@400;600;700;800&display=swap">
<style>
:root{
  --blue:#1f6ca9;
  --blue-dark:#174f80;
  --navy:#1d3557;
  --green:#5aae3a;
  --ink:#2b2b2b;
  --grey-text:#555;
  --panel:#efeeee;
  --white:#fff;
  --line:#dcdcdc;
}
*{box-sizing:border-box;margin:0;padding:0}
html,body{width:1200px;height:3936px;overflow:hidden}
body{font-family:"Open Sans",sans-serif;color:var(--ink);background:var(--white);position:relative}
.abs{position:absolute}

/* header */
.site-header{position:absolute;left:0;top:0;width:1200px;height:133px;background:var(--white)}
.brand{position:absolute;left:130px;top:30px}
.brand-tag{font-size:11px;color:var(--blue);margin-left:42px}
.brand-name{display:flex;align-items:center;gap:10px;font-size:40px;font-weight:700;color:var(--blue);letter-spacing:-1px;line-height:1.1}
.brand-dot{width:30px;height:30px;border-radius:50%;background:var(--green)}
.follow{position:absolute;left:778px;top:40px;display:flex;align-items:center;gap:6px;font-size:10px;font-weight:700}
.follow span.c{width:24px;height:24px;border-radius:50%;background:var(--blue);display:inline-block}
.follow span.c.d{background:var(--navy)}
.login{position:absolute;left:980px;top:32px;width:85px;height:34px;border:2px solid var(--blue);color:var(--blue);font-size:12px;font-weight:600;display:flex;align-items:center;justify-content:center}
.main-nav{position:absolute;left:453px;top:96px;display:flex;gap:26px;font-size:12.5px;font-weight:600;color:#222}
.main-nav .on{color:var(--green)}

/* hero */
.hero{position:absolute;left:0;top:133px;width:1200px;height:555px;background:linear-gradient(180deg,#b9cfe0 0%,#9db6c9 35%,#4a4b55 70%,#242428 100%)}
.hero-title{position:absolute;left:382px;top:64px;width:420px;height:103px;background:rgba(255,255,255,.85);text-align:center;font-size:38px;font-weight:800;color:var(--blue);line-height:1.3;padding-top:5px}
.hero-arrow{position:absolute;top:256px;width:42px;height:46px;background:rgba(0,0,0,.5);display:flex;align-items:center;justify-content:center}

/* category bar */
.topics{position:absolute;left:0;top:688px;width:1200px;height:97px;background:var(--blue);display:flex}
.topic{height:97px;display:flex;align-items:center;justify-content:center;gap:12px;color:var(--white);font-weight:700;font-size:17px;border-right:1px solid rgba(255,255,255,.25)}
.topic:last-child{border-right:0}

/* welcome */
.welcome-photo{position:absolute;left:0;top:785px;width:637px;height:564px;background:linear-gradient(135deg,#d9d2c8,#c6a98e 45%,#a98a73 80%,#8a7564)}
.welcome{position:absolute;left:637px;top:785px;width:563px;height:564px;background:var(--panel)}
.welcome .rule{position:absolute;left:64px;top:60px;width:38px;height:3px;background:var(--blue-dark)}
.welcome h3{position:absolute;left:64px;top:76px;font-size:19px;font-weight:700}
.welcome h2{position:absolute;left:64px;top:96px;font-size:42px;font-weight:800;color:#333}
.welcome p{position:absolute;left:64px;width:410px;font-size:17.5px;line-height:1.47;color:#333}
.btn-blue{position:absolute;left:64px;top:447px;width:116px;height:39px;background:var(--blue-dark);color:var(--white);font-size:13px;font-weight:700;display:flex;align-items:center;justify-content:center}

/* guide cards */
.guide{position:absolute;left:128px;width:470px;height:216px;border:2px solid var(--line);background:var(--white)}
.guide .ico{position:absolute;left:27px;top:30px;width:89px;height:89px;border-radius:50%;background:var(--blue-dark);display:flex;align-items:center;justify-content:center}
.guide h4{position:absolute;left:142px;top:27px;font-size:15px;font-weight:700;line-height:1.15;color:#222}
.guide p{position:absolute;left:142px;width:290px;font-size:13px;line-height:1.5;color:#444}
.guide .go{position:absolute;right:-2px;bottom:-2px;width:36px;height:32px;background:var(--blue-dark);border-radius:18px 0 0 0;display:flex;align-items:center;justify-content:center}
.checklist{position:absolute;left:638px;top:1397px;width:428px;height:590px;background:linear-gradient(180deg,#eef4fb 0 52px,#8fc4ea 52px,#78b5e3 520px,#eef4fb 520px)}

/* testimonials */
.voices{position:absolute;left:0;top:2133px;width:1200px;height:507px;background:linear-gradient(180deg,#1e67a3,#1a5a92)}
.voices h2{position:absolute;left:0;top:62px;width:1200px;text-align:center;color:var(--white);font-size:31px;font-weight:800}
.quote{position:absolute;top:148px;width:444px;height:299px;background:var(--white)}
.quote .mk{position:absolute;font-size:42px;font-weight:800;color:var(--blue-dark);line-height:1}
.quote p{position:absolute;left:75px;top:40px;width:325px;font-size:16px;line-height:1.42;color:#444}
.quote .rule{position:absolute;left:75px;top:235px;width:46px;height:2px;background:var(--blue)}
.quote .who{position:absolute;left:75px;top:256px;font-size:14px;font-weight:700;color:var(--blue)}
.v-arrow{position:absolute;top:278px}

/* blog */
.blog-title{position:absolute;left:0;top:2690px;width:1200px;text-align:center;font-size:32px;font-weight:800;color:#222}
.post{position:absolute;top:2789px;width:296px;height:401px;background:var(--white);box-shadow:0 2px 8px rgba(0,0,0,.12)}
.post .img{height:213px}
.post h5{position:absolute;left:27px;top:233px;font-size:18px;font-weight:700;line-height:1.3;color:#222;border-left:6px solid var(--green);padding-left:21px;margin-left:-27px}
.post p{position:absolute;left:27px;top:298px;width:245px;font-size:13.5px;line-height:1.45;color:#444}

/* call to action */
.cta{position:absolute;left:0;top:3250px;width:1200px;height:376px;background:radial-gradient(ellipse at 55% 60%,#3b4658,#1b1d22 70%)}
.cta h2{position:absolute;left:0;top:113px;width:1200px;text-align:center;color:var(--white);font-size:29px;font-weight:800;line-height:1.33}
.btn-green{position:absolute;left:490px;top:205px;width:220px;height:57px;background:var(--green);color:var(--white);font-size:22px;font-weight:800;display:flex;align-items:center;justify-content:center}

/* footer */
.site-footer{position:absolute;left:0;top:3626px;width:1200px;height:310px;background:var(--blue)}
.site-footer .brand{left:130px;top:80px}
.site-footer .brand-tag{color:var(--white);font-size:13px}
.site-footer .brand-name{color:var(--white);font-size:54px}
.site-footer .brand-dot{background:var(--white);width:36px;height:36px}
.f-col{position:absolute;top:52px;color:var(--white);font-size:11px;line-height:1.65}
.f-col h6{font-size:11.5px;font-weight:700;margin-bottom:18px}
.f-row{display:flex;gap:14px;align-items:flex-start;margin-bottom:20px}
.soc{display:flex;gap:14px;align-items:center;margin-bottom:13px}
.soc i{width:26px;height:26px;border-radius:50%;background:var(--navy);display:inline-block}
.copy{position:absolute;left:0;top:274px;width:1200px;text-align:center;color:var(--white);font-size:11px}
</style>
</head>
<body>

<header class="site-header">
  <div class="brand">
    <div class="brand-tag">Take charge of your change</div>
    <div class="brand-name">Varsity Purse <span class="brand-dot"></span></div>
  </div>
  <div class="follow">FOLLOW US&nbsp; <span class="c"></span><span class="c"></span><span class="c d"></span></div>
  <div class="login">LOGIN</div>
  <nav class="main-nav">
    <span class="on">HOME</span><span>TAKE THE PLEDGE</span><span>BLOG</span><span>ABOUT US</span><span>TIPS &amp; TRICKS</span><span>ABOUT NUVOE</span>
  </nav>
</header>

<section class="hero" role="img" aria-label="Graduates in caps and gowns raising diplomas against a bright sky">
  <div class="hero-title">TAKE CHARGE<br>OF YOUR CHANGE</div>
  <div class="hero-arrow" style="left:0"><svg width="14" height="20"><path d="M11 2 3 10l8 8" stroke="#fff" stroke-width="2" fill="none"/></svg></div>
  <div class="hero-arrow" style="right:0"><svg width="14" height="20"><path d="M3 2l8 8-8 8" stroke="#fff" stroke-width="2" fill="none"/></svg></div>
</section>

<nav class="topics">
  <div class="topic" style="width:206px"><svg width="28" height="28"><circle cx="14" cy="9" r="6" fill="none" stroke="#fff" stroke-width="2.5"/><path d="M3 22h14l7-5" stroke="#fff" stroke-width="3" fill="none"/></svg>BUDGETING</div>
  <div class="topic" style="width:183px"><svg width="32" height="28"><ellipse cx="16" cy="16" rx="12" ry="9" fill="#fff"/><circle cx="16" cy="5" r="3.5" fill="#fff"/></svg>SAVING</div>
  <div class="topic" style="width:260px"><svg width="26" height="30"><circle cx="13" cy="8" r="7" fill="#fff"/><path d="M1 30a12 12 0 0 1 24 0z" fill="#fff"/></svg>PERSONAL STORIES</div>
  <div class="topic" style="width:151px"><svg width="22" height="30"><circle cx="11" cy="11" r="9" fill="#fff"/><rect x="7" y="21" width="8" height="6" fill="#fff"/></svg>TIPS</div>
  <div class="topic" style="width:197px"><svg width="30" height="28"><path d="M2 26h26" stroke="#fff" stroke-width="2"/><rect x="5" y="16" width="4" height="9" fill="#fff"/><rect x="12" y="11" width="4" height="14" fill="#fff"/><rect x="19" y="6" width="4" height="19" fill="#fff"/><path d="M3 14 14 6l4 3 9-7" stroke="#fff" stroke-width="2" fill="none"/></svg>GROWTH</div>
  <div class="topic" style="width:203px"><svg width="30" height="30"><path d="M25 11A11 11 0 0 0 5 10M5 19a11 11 0 0 0 20 1" stroke="#fff" stroke-width="3" fill="none"/><path d="M26 4v8h-8M4 26v-8h8" stroke="#fff" stroke-width="2.5" fill="none"/></svg>CHANGE</div>
</nav>

<div class="welcome-photo" role="img" aria-label="Group of smiling students giving thumbs up"></div>
<section class="welcome">
  <div class="rule"></div>
  <h3>WELCOME TO</h3>
  <h2>VARSITY PURSE</h2>
  <p style="top:173px">Varsity Purse will teach you how to use your student loan to get a new car, how to fill out those first day of work tax forms without calling mom and dad,and how to build credit without getting into credit card debt.</p>
  <p style="top:332px">Personal financial skills will keep your wallet full and your options open. Take charge of your finances today!</p>
  <div class="btn-blue">READ MORE</div>
</section>

<article class="guide" style="top:1397px">
  <div class="ico"><svg width="46" height="46"><circle cx="26" cy="14" r="10" fill="none" stroke="#fff" stroke-width="3"/><text x="26" y="19" font-size="14" font-weight="700" fill="#fff" text-anchor="middle" font-family="Open Sans,sans-serif">$</text><path d="M4 32h14l6 4 16-8" stroke="#fff" stroke-width="4" fill="none"/></svg></div>
  <h4>HOW TO BUDGET</h4>
  <p style="top:52px">Having a solid budget is a fundamental building block in becoming financially independent, so here is a breakdown of the purpose behind budgeting and how to create and stick to your own budget. Budgeting can be a wonderful thing if you allow it to be. A budget is...</p>
  <div class="go"><svg width="12" height="14"><path d="M3 2l6 5-6 5" stroke="#fff" stroke-width="2.5" fill="none"/></svg></div>
</article>
<article class="guide" style="top:1625px">
  <div class="ico"><svg width="48" height="46"><path d="M4 18 24 4l20 14" stroke="#fff" stroke-width="4" fill="none"/><rect x="10" y="20" width="28" height="22" fill="#fff"/><text x="24" y="38" font-size="17" font-weight="800" fill="#174f80" text-anchor="middle" font-family="Open Sans,sans-serif">$</text></svg></div>
  <h4 style="top:28px">MONEY SAVING HACKS<br>FOR MILLENNIALS</h4>
  <p style="top:70px">The other generations love to pick on us, but the unemployment rate is the lowest it's been in over 50 years, so it's good to be a millennial! We're barely 20 and already making money, here are the average starting salaries...</p>
  <div class="go"><svg width="12" height="14"><path d="M3 2l6 5-6 5" stroke="#fff" stroke-width="2.5" fill="none"/></svg></div>
</article>
<article class="guide" style="top:1854px">
  <div class="ico"><svg width="48" height="44"><path d="M24 42 5 22A11 11 0 0 1 24 8a11 11 0 0 1 19 14z" fill="#fff"/><text x="24" y="31" font-size="19" font-weight="800" fill="#174f80" text-anchor="middle" font-family="Open Sans,sans-serif">$</text></svg></div>
  <h4 style="top:36px">HOW TO CREATE YOUR OWN<br>SIDE HUSTLE</h4>
  <p style="top:78px">So, you're thinking of starting a side hustle, but before you do you should think about a few things. By definition, side hustles are any type of employment undertaken in addition to one's full-time job. That's...</p>
  <div class="go"><svg width="12" height="14"><path d="M3 2l6 5-6 5" stroke="#fff" stroke-width="2.5" fill="none"/></svg></div>
</article>

<div class="checklist" role="img" aria-label="Dorm &amp; Den and Varsity Purse money checklist infographic covering banking, taxes, applications, parental guidance, real world, cash, work and adulting topics"></div>

<section class="voices">
  <h2>DON'T TAKE OUR WORD FOR IT…</h2>
  <svg class="v-arrow" style="left:72px" width="14" height="22"><path d="M11 2 3 11l8 9" stroke="#fff" stroke-width="3" fill="none"/></svg>
  <svg class="v-arrow" style="left:1104px" width="14" height="22"><path d="M3 2l8 9-8 9" stroke="#fff" stroke-width="3" fill="none"/></svg>
  <div class="quote" style="left:131px">
    <span class="mk" style="left:40px;top:30px">“</span>
    <p>Believe it or not, I was fifty before I understood the difference between gross and net profit. Where was Varsity Purse when I needed it? <b style="font-size:30px;color:#174f80;vertical-align:-10px">”</b></p>
    <div class="rule"></div>
    <div class="who">Marcus Hale, Founder of Northwind Air</div>
  </div>
  <div class="quote" style="left:620px">
    <span class="mk" style="left:40px;top:30px">“</span>
    <p>In today's extra competitive job market, college students need a leg up. Financial literacy skills, like those taught at Varsity Purse, are the answer. Financial literacy provides an important advantage in finding a job and is a skill that will help students throughout their lives. <b style="font-size:30px;color:#174f80;vertical-align:-10px">”</b></p>
    <div class="rule"></div>
    <div class="who">Lena Ortiz, Personal Finance Expert</div>
  </div>
</section>

<h2 class="blog-title">LATEST BLOG</h2>
<article class="post" style="left:129px">
  <div class="img" role="img" aria-label="Hands holding a pink piggy bank" style="background:linear-gradient(135deg,#c7a48c,#e7c3c6 50%,#8a6b55)"></div>
  <h5>Money Saving Hacks<br>For Millennials</h5>
  <p>The other generations love to pick on us, but the unemployment rate is the lowest it's been in over 50 years, so it's good to be a millennial!</p>
</article>
<article class="post" style="left:452px">
  <div class="img" role="img" aria-label="Traveler photographing old stone arches" style="background:linear-gradient(160deg,#dfe6ec,#c9b89a 55%,#6d7f96)"></div>
  <h5>How You Can Afford<br>To Travel</h5>
  <p>If you wait until the last minute, you're basically asking to spend an arm and a leg on travel expenses..</p>
</article>
<article class="post" style="left:770px">
  <div class="img" role="img" aria-label="Hands counting a stack of banknotes" style="background:linear-gradient(135deg,#3e4650,#9aa68d 55%,#5d6a5a)"></div>
  <h5>How To Create Your<br>Own Side Hustle</h5>
  <p>So, you're thinking of starting a side hustle, but before you do you should think about a few things.</p>
</article>

<section class="cta" role="img" aria-label="Dim photo of a payment card on a table">
  <h2>USING PEER-TO-PEER TIPS, PERSONAL STORIES AND<br>NUVOE, YOU CAN BECOME A VARSITY PURSE!</h2>
  <div class="btn-green">CONTACT US</div>
</section>

<footer class="site-footer">
  <div class="brand">
    <div class="brand-tag">Take charge of your change</div>
    <div class="brand-name">Varsity Purse <span class="brand-dot"></span></div>
  </div>
  <div class="f-col" style="left:530px">
    <h6>CONTACT US</h6>
    <div class="f-row"><svg width="10" height="14"><path d="M5 14 1 7a4 4 0 1 1 8 0z" fill="#fff"/></svg><span>2150 Maple Row<br>Fairview, CA 90210</span></div>
    <div class="f-row"><svg width="10" height="12"><path d="M2 1h3l1 3-2 1a7 7 0 0 0 3 3l1-2 3 1v3c-5 1-10-4-9-9z" fill="#fff"/></svg><span>555.010.4477</span></div>
    <div class="f-row"><svg width="12" height="10"><rect width="12" height="9" fill="#fff"/><path d="M0 0l6 5 6-5" stroke="#1f6ca9" fill="none"/></svg><span>hello@varsitypurse.com</span></div>
  </div>
  <div class="f-col" style="left:766px">
    <h6>MENU</h6>
    HOME<br>TAKE THE PLEDGE<br>BLOG<br>ABOUT US<br>TIPS &amp; TRICKS<br>ABOUT NUVOE<br>LOGIN
  </div>
  <div class="f-col" style="left:952px">
    <h6>CONNECT WITH US</h6>
    <div class="soc"><i></i>Friendly</div>
    <div class="soc"><i></i>Chirper</div>
    <div class="soc"><i></i>Linkwork</div>
  </div>
  <div class="copy">Copyrights @ 2019 All Rights Reserved</div>
</footer>

</body>
</html>
```